Wordpress Design Project for Bankruptcy Law Office in San Francisco

our current website: www.dorvanelilaw-example.com

we would like to re-design it for wordpress to make it faster and a bit more modern.

content should be similar to what we have there right now but also we do family law

please include logo for law office:

Law Office of Marta K. Dolvenidze

Thank you.
Updates

please see attached word document with logos that we like as an example.

we do tend to like color red.  darker red.

Please submit your design variations and logo as soon as possible.   We would like to go over them and make our decision

Reason: Please create couple of more variations of logo for your design, so we can make our decision what we like the most. Please see word doc for samples: Text: Law Office Of Marta K. Dolvenidze

Reason: final touches

Target Market(s)

bankruptcy and family law clients

Industry/Entity Type

Family Law

Requirements
Must have
• see examples of law sites
http://promo.lexorbin-example.com/testimonials

- new logo: Law Office of Marta K. Dolvenidze
- client intake form
- blog
- contact us form

Nice to have
• - map
- red color
- on the front page a nice photo of SF or a happy family

```html
<!DOCTYPE html>
<html lang="en">
<head>
<meta charset="utf-8">
<title>Dolvenidze Law – Complete Bankruptcy Information</title>
<link rel="stylesheet" href="https://fonts.googleapis.com/css2?family=PT+Sans:ital,wght@0,400;0,700;1,400&display=swap">
<style>
:root{
  --ink:#222;
  --body:#3a3a3a;
  --brand:#2a6d96;
  --brand-dark:#1c4d6d;
  --nav-top:#3483ab;
  --nav-bottom:#1f6088;
  --link:#1f6591;
  --band:#f4f5f6;
  --side:#2b6488;
  --side-head:#1d4a68;
  --btn:#173a52;
  --foot:#ececec;
  --rule:#bbb;
}
*{box-sizing:border-box;margin:0;padding:0}
html,body{width:712px;height:1200px;overflow:hidden;background:#fff}
body{font-family:"PT Sans",sans-serif;color:var(--body);position:relative}
.topline{height:3px;background:var(--brand-dark)}
.header{position:relative;height:86px}
.brand{position:absolute;left:18px;top:30px}
.brand-name{display:flex;align-items:center;gap:7px;font-size:26px;font-weight:700;color:var(--brand);line-height:1}
.brand-mark{width:11px;height:11px;background:var(--brand)}
.brand-tag{font-size:9px;color:var(--link);margin-top:8px}
.lang{position:absolute;right:20px;top:18px;display:flex;align-items:center;gap:5px;font-size:8.5px;color:var(--link)}
.lang-box{width:77px;height:17px;background:#e3ebf1;color:#333;padding:3px 5px;position:relative}
.lang-box::after{content:"";position:absolute;right:7px;top:7px;border:3px solid transparent;border-top-color:#333}
.call{position:absolute;right:20px;top:56px;font-size:11px;color:var(--link)}
.call b{font-size:16px;font-weight:400;color:#111;margin-left:4px}
.nav{height:30px;background:linear-gradient(var(--nav-top),var(--nav-bottom));display:flex}
.nav a{color:#fff;text-decoration:none;font-size:10px;line-height:30px;padding:0 16px;border-right:1px solid #2a6b93}
.nav a:first-child{padding:0 22px 0 30px;background:rgba(0,0,0,.08)}
.hero{height:245px;background:linear-gradient(100deg,#c9b89a 0%,#e9dfc8 35%,#d8c4a4 60%,#a9c79b 100%)}
.services{height:176px;background:var(--band);display:flex;padding:21px 0 0 14px;gap:19px}
.service{width:157px}
.service h3{font-size:11px;font-weight:700;color:var(--ink);margin-bottom:5px;padding-left:3px}
.service .photo{height:67px;border:2px solid #fff;box-shadow:0 0 2px #999;margin-bottom:10px}
.service h4{font-size:9.5px;color:var(--link);padding-left:1px}
.service p{font-size:7.5px;line-height:1.5;color:var(--link);padding-left:1px}
.main{position:absolute;left:0;top:540px;width:496px;padding:16px 12px 0 12px}
.main h2{font-size:11.5px;font-weight:700;color:#111;letter-spacing:.2px;margin-bottom:9px}
.main p{font-size:7.5px;line-height:1.68;margin-bottom:4px}
.main h5{font-size:7.5px;font-weight:700;color:#222;margin:5px 0 4px}
.divider{border-top:1px dotted var(--rule);margin:14px 0 14px}
.story{display:flex;gap:9px;margin:10px 0 6px}
.story .photo{width:152px;height:100px;flex:none}
.story h4{font-size:9.5px;color:var(--link);margin:0 0 3px}
.story p{margin-bottom:3px}
.sidebar{position:absolute;left:506px;top:540px;width:206px;height:610px;background:var(--side);color:#fff}
.side-head{height:29px;background:var(--side-head);border-bottom:2px solid #3a7aa0;font-size:13px;font-variant:small-caps;padding:6px 12px}
.form{padding:4px 12px 0 12px}
.form label{display:block;font-size:8px;margin:3px 0 2px}
.form .field{height:17px;background:#fff;margin-bottom:9px}
.form .area{height:47px;background:#fff;margin-bottom:6px}
.copy{display:flex;align-items:center;gap:6px;font-size:7.5px}
.copy span{width:8px;height:8px;background:#dfe7ec}
.buttons{display:flex;gap:9px;margin:9px 0 13px}
.buttons span{background:var(--btn);font-size:7.5px;font-weight:700;padding:4px 11px;border-radius:2px}
.news{padding:8px 14px 0 14px}
.news h4{font-size:9.5px;font-weight:400;margin-top:8px}
.news p{font-size:7.5px;font-style:italic;line-height:1.55}
.news a{display:block;color:#fff;text-decoration:none;font-size:7.5px;font-weight:700;margin:4px 0 6px}
.footer{position:absolute;left:0;top:1150px;width:712px;height:34px;background:var(--foot);font-size:7.5px;color:#333;display:flex;justify-content:space-between;align-items:center;padding:0 15px}
</style>
</head>
<body>
<div class="topline"></div>
<header class="header">
  <div class="brand">
    <div class="brand-name"><span class="brand-mark"></span>Dolvenidze Law</div>
    <div class="brand-tag">Law Office of Marta K. Dolvenidze</div>
  </div>
  <div class="lang">Select Language <div class="lang-box">English</div></div>
  <div class="call">CALL US NOW: <b>(555) 014-2290</b></div>
</header>
<nav class="nav">
  <a href="#">HOME</a><a href="#">ABOUT US</a><a href="#">AREAS OF PRACTISE</a><a href="#">RESOURCES</a><a href="#">BLOG</a><a href="#">FAQ</a><a href="#" style="border:0">CONTACT US</a>
</nav>
<div class="hero" role="img" aria-label="Photo of a smiling multigenerational family outdoors"></div>

<section class="services">
  <div class="service"><h3>Debt Relief</h3><div class="photo" role="img" aria-label="Photo of a relieved man lying on grass among papers" style="background:linear-gradient(#9fb76a,#6f8c3c)"></div><h4>Tittle goes here</h4><p>Lorem ipsum dolor sit amet, consectetur adipisicing elit, sed do eiusmod tempor incididunt ut labore et dolore magna</p></div>
  <div class="service"><h3>Fore Closure Prevention</h3><div class="photo" role="img" aria-label="Photo of a for-sale sign on a white fence" style="background:linear-gradient(90deg,#d8d8d4,#c33a3a 45%,#b52e2e 70%,#e2e2de)"></div><h4>Tittle goes here</h4><p>Lorem ipsum dolor sit amet, consectetur adipisicing elit, sed do eiusmod tempor incididunt ut labore et dolore magna</p></div>
  <div class="service"><h3>Chapter 13</h3><div class="photo" role="img" aria-label="Photo of an open law book on a desk" style="background:linear-gradient(#6b3a1f,#c9a27a 60%,#7a4a28)"></div><h4>Tittle goes here</h4><p>Lorem ipsum dolor sit amet, consectetur adipisicing elit, sed do eiusmod tempor incididunt ut labore et dolore magna</p></div>
  <div class="service"><h3>Chapter 7</h3><div class="photo" role="img" aria-label="Photo of a shelf of leather-bound law books" style="background:linear-gradient(90deg,#3a2418,#8a5a34 50%,#4a2e1c)"></div><h4>Tittle goes here</h4><p>Lorem ipsum dolor sit amet, consectetur adipisicing elit, sed do eiusmod tempor incididunt ut labore et dolore magna</p></div>
</section>

<main class="main">
  <h2>WELCOME TO DOLVENIDZE LAW - COMPLETE BANKRUPTCY INFORMATION</h2>
  <p>The Law Offices of Marta K. Dolvenidze is a consumer law office dedicated to consumer protection and zealously defending the rights of our clients. We offer the big firm quality legal representation with a small firm individualized attention to each client.</p>
  <p>Our office offers services in: all types of consumer bankruptcy filings, i.e. Chapter 7, Chapter 13, Chapter 11, negotiating a settlement of your debts, assisting you in the defense of collection litigation and defending you against foreclosure. Please review our site and see what we may be able to offer you. Feel free to call us at (555) 018-3344 or use our free case evaluation form.</p>
  <h5>Speak to a Lawyer</h5>
  <p>Unlike some other law firms, when you call the Law Office of Marta K. Dolvenidze you will speak to an actual attorney. Not a paralegal or assistant. And even after retaining our office you will still speak to an attorney unlike other firms where you cannot get a hold of your attorney after several attempts.</p>
  <p style="margin-top:8px">Lorem ipsum dolor sit amet, consectetuer adipiscing elit. Nam cursus. Morbi ut mi. Nullam enim leo, egestas id, condimentum at, laoreet mattis, massa. Sed eleifend nonummy diam. Praesent mauris ante, elementum et, bibendum at, posuere sit amet, nibh. Duis tincidunt lectus quis dui viverra vestibulum. Suspendisse vulputate aliquam dui. Nulla elementum dui ut augue. Aliquam vehicula mi at mauris. Maecenas placerat, nisl at consequat rhoncus, sem nunc gravida justo, quis eleifend arcu velit quis lacus. Morbi magna magna, tincidunt a, mattis non, imperdiet vitae</p>
  <div class="divider"></div>
  <h2 style="padding-left:4px">STORIES &amp; MORE INFORMATION</h2>
  <article class="story">
    <div class="photo" role="img" aria-label="Photo of a judge's gavel on a law book" style="background:linear-gradient(135deg,#3a1a10,#8a4a22 55%,#2a140c)"></div>
    <div><h4>Story TItle line goes here</h4>
    <p>Lorem ipsum dolor sit amet, consectetuer adipiscing elit. Nam cursus. Morbi ut mi. Nullam enim leo, egestas id, condimentum at, laoreet mattis, massa.</p>
    <p>Sed eleifend nonummy diam. Praesent mauris ante, elementum et, bibendum at, posuere sit amet, nibh. Duis tincidunt lectus quis dui viverra vestibulum. Suspendisse vulputate aliquam dui. Nulla elementum dui ut augue. Aliquam vehicula mi at mauris. Maecenas placerat, nisl at consequat rhoncus, sem nunc gravida justo, quis eleifend arcu velit quis lacus. Morbi magna magna, tincidunt a, mattis non, imperdiet vitae, tellus.</p></div>
  </article>
  <p>Mauris vel lacus vitae felis vestibulum volutpat. Etiam est nunc, venenatis in, tristique eu, imperdiet ac, nisl. Cum sociis natoque penatibus et magnis dis parturient montes, nascetur ridiculus mus. In iaculis facilisis massa.</p>
  <article class="story" style="margin-top:22px">
    <div class="photo" role="img" aria-label="Photo of a family with children on bicycles in a park" style="background:linear-gradient(#cfd9b0,#b0453a 55%,#8fa86a)"></div>
    <div><h4>Story TItle line goes here</h4>
    <p>Lorem ipsum dolor sit amet, consectetuer adipiscing elit. Nam cursus. Morbi ut mi. Nullam enim leo, egestas id, condimentum at, laoreet mattis, massa.</p>
    <p>Sed eleifend nonummy diam. Praesent mauris ante, elementum et, bibendum at, posuere sit amet, nibh. Duis tincidunt lectus quis dui viverra vestibulum. Suspendisse vulputate aliquam dui. Nulla elementum dui ut augue. Aliquam vehicula mi at mauris. Maecenas placerat, nisl at consequat rhoncus, sem nunc gravida justo, quis eleifend arcu velit quis lacus. Morbi magna magna, tincidunt a, mattis non, imperdiet vitae, tellus.</p></div>
  </article>
  <p>Mauris vel lacus vitae felis vestibulum volutpat. Etiam est nunc, venenatis in, tristique eu, imperdiet ac, nisl. Cum sociis natoque penatibus et magnis dis parturient montes, nascetur ridiculus mus. In iaculis facilisis massa.</p>
</main>

<aside class="sidebar">
  <div class="side-head">Contact Form</div>
  <div class="form">
    <label>Name:</label><div class="field"></div>
    <label>Email:</label><div class="field"></div>
    <label>Phone:</label><div class="field"></div>
    <label>Subject:</label><div class="field"></div>
    <label>Message:</label><div class="area"></div>
    <div class="copy"><span></span>Send a copy of this message to yourself</div>
    <div class="buttons"><span>SEND</span><span>RESET</span></div>
  </div>
  <div class="side-head">Recent Blog &amp; News</div>
  <div class="news">
    <h4>Tittle line here</h4>
    <p>Lorem ipsum dolor sit amet, consectetuer adipiscing elit. Nam cursus. Morbi ut mi. Nullam enim leo, egestas id, condimentum at, laoreet mattis, massa.</p>
    <a href="#">LEARN MORE</a>
    <h4>Tittle line here</h4>
    <p>Lorem ipsum dolor sit amet, consectetuer adipiscing elit. Nam cursus. Morbi ut mi. Nullam enim leo, egestas id, condimentum at, laoreet mattis, massa.</p>
    <a href="#">LEARN MORE</a>
    <h4>Tittle line here</h4>
    <p>Proin dui lectus, cursus eu, mattis laoreet, viverra sit amet, quam. Curabitur vel dolor ultrices ipsum dictum tristique. Praesent vitae lacus. Ut velit enim, vestibulum non, fermentum nec, hendrerit quis, leo. Pellentesque rutrum malesuada neque.</p>
    <a href="#">LEARN MORE</a>
  </div>
</aside>

<footer class="footer">
  <div>© 2012 Company Name &nbsp;|&nbsp; All right reserved &nbsp;|&nbsp; Term &amp; Conditions</div>
  <div>HOME &nbsp;|&nbsp; ABOUT US &nbsp;|&nbsp; AREAS OF PRACTISE &nbsp;|&nbsp; RESOURCES &nbsp;|&nbsp; BLOG &nbsp;|&nbsp; FAQ &nbsp;|&nbsp; CONTACT US</div>
</footer>
</body>
</html>
```